Modern looking signage for dental office.

Exterior signage for passing cars
Updates
Need extra days to review
Target Market(s)
Cars passing by
Font styles to use
Sans Serif
Colors
3276b5
Requirements
Must have
- Logo
- OPEN ON SUTURDAY AND SUNDAY
- NIGHT CLINIC AVAILABLE
- PLEASE USE THE FONT TYPE IN FILE 4 UPLOADED BELOW.
- (847) 302-7469
- Modern looking

```html
<!DOCTYPE html>
<html lang="en">
<head>
<meta charset="UTF-8">
<title>Nova Dental – Exterior Sign</title>
<link rel="stylesheet" href="https://fonts.googleapis.com/css2?family=Arimo:wght@400&family=Jost:wght@400&family=Roboto+Condensed:wght@400&display=swap">
<style>
  :root {
    --brand-blue: #03569a;
    --ink-dark: #4a4442;
    --ink-phone: #231f20;
    --frame-grey: #8a8a8a;
    --paper: #ffffff;
  }
  html, body {
    margin: 0;
    padding: 0;
    width: 1200px;
    height: 1200px;
    overflow: hidden;
    background: var(--paper);
  }
  .sign {
    display: block;
    width: 1200px;
    height: 1200px;
  }
  .panel-frame { fill: var(--paper); stroke: var(--frame-grey); stroke-width: 1; }
  .blue-band { fill: var(--brand-blue); }
  .brand-ring { fill: none; stroke: var(--ink-dark); stroke-width: 2.5; }
  .brand-name {
    font-family: "Jost", sans-serif;
    font-weight: 400;
    font-size: 92px;
    fill: var(--ink-dark);
  }
  .brand-tagline {
    font-family: "Roboto Condensed", sans-serif;
    font-size: 37px;
    fill: var(--ink-dark);
  }
  .band-text {
    font-family: "Arimo", sans-serif;
    fill: var(--paper);
    letter-spacing: 1px;
  }
  .band-text--large { font-size: 54px; }
  .band-text--small { font-size: 41px; }
  .phone-number {
    font-family: "Arimo", sans-serif;
    font-size: 41px;
    fill: var(--ink-phone);
  }
  .phone-icon-ring { fill: none; stroke: var(--brand-blue); stroke-width: 3; }
  .phone-icon-handset { fill: var(--brand-blue); }
</style>
</head>
<body>
<svg class="sign" viewBox="0 0 1200 1200" xmlns="http://www.w3.org/2000/svg">
  <g class="main-panel">
    <rect class="panel-frame" x="185" y="332" width="831" height="410"/>
    <polygon class="blue-band" points="486,574 1016,574 1016,742 581,742"/>

    <g class="brand">
      <circle class="brand-ring" cx="338" cy="464" r="76"/>
      <text class="brand-name" x="432" y="498" textLength="542" lengthAdjust="spacingAndGlyphs">NOVA DENTAL</text>
      <text class="brand-tagline" x="484" y="547" textLength="418" lengthAdjust="spacingAndGlyphs">MODERN GENERAL DENTISTRY</text>
    </g>

    <g class="opening-days" text-anchor="end">
      <text class="band-text band-text--large" x="966" y="622" textLength="236" lengthAdjust="spacingAndGlyphs">OPEN ON</text>
      <text class="band-text band-text--large" x="966" y="676" textLength="402" lengthAdjust="spacingAndGlyphs">SATURDAY AND</text>
      <text class="band-text band-text--large" x="966" y="730" textLength="216" lengthAdjust="spacingAndGlyphs">SUNDAY</text>
    </g>
  </g>

  <g class="contact-strip">
    <rect class="panel-frame" x="185" y="764" width="831" height="102"/>
    <polygon class="blue-band" points="589,764 1016,764 1016,866 645,866"/>

    <g class="phone-icon">
      <circle class="phone-icon-ring" cx="236" cy="815" r="23"/>
      <path class="phone-icon-handset" d="M226 802 c2-2 5-2 6 0 l4 6 c1 2 0 4-1 5 l-2 2 c2 5 6 9 11 11 l2-2 c1-1 3-2 5-1 l6 4 c2 1 2 4 0 6 l-3 3 c-3 3-9 2-16-3 c-7-5-12-11-14-18 c-1-4 0-8 2-10 z"/>
    </g>
    <text class="phone-number" x="278" y="830" textLength="304" lengthAdjust="spacingAndGlyphs">(847) 302-7469</text>

    <g class="night-clinic" text-anchor="end">
      <text class="band-text band-text--small" x="966" y="808" textLength="281" lengthAdjust="spacingAndGlyphs">NIGHT CLINIC</text>
      <text class="band-text band-text--small" x="966" y="851" textLength="224" lengthAdjust="spacingAndGlyphs">AVAILABLE</text>
    </g>
  </g>
</svg>
</body>
</html>
```